Private Investigation Business Card Design

I need a business card for a new private investigation company named Brisk Inquiries. I perform mainly surveillance jobs, vehicle repossessions, document serves etc. The final design should aim for a professional look. The logo has a magnifying glass with stick man arms and legs and is in a running action to show the "Brisk" aspect of the name. If the colour scheme could remain the same as the website www.briskinquiries-demo.com.au with silvers,blacks and a couple electric blue highlights.
Industry/Entity Type
Business
Contact Information for Business Card
Morgan Kellaway
Brisk Inquiries
0487316204
PO Box 58, Carnwell NSW 2291
info@briskinquiries-demo.com.au
www.briskinquiries-demo.com.au
Look and feel

```html
<!DOCTYPE html>
<html lang="en">
<head>
<meta charset="utf-8">
<title>Brisk Inquiries – Business Card</title>
<link rel="stylesheet" href="https://fonts.googleapis.com/css2?family=Arimo:wght@400;700&display=swap">
<style>
  :root {
    --stage: #2b2b2b;
    --card-white: #ffffff;
    --silver-light: #dcdcdc;
    --silver-mid: #a9a9ab;
    --silver-dark: #8a8a8d;
    --ink: #2e2e2e;
    --ink-soft: #6a6a6a;
    --ink-faint: #8c8c8c;
    --accent: #b9b9bb;
  }
  * { margin: 0; padding: 0; box-sizing: border-box; }
  html, body { width: 1200px; height: 750px; overflow: hidden; }
  body {
    background: var(--stage);
    font-family: "Arimo", Arial, sans-serif;
    position: relative;
  }
  .card {
    position: absolute;
    top: 215px;
    width: 520px;
    height: 310px;
    border-radius: 3px;
    overflow: hidden;
  }
  /* Back face */
  .card--back {
    left: 50px;
    background: radial-gradient(ellipse at 50% 42%, var(--silver-light) 0%, var(--silver-mid) 60%, var(--silver-dark) 100%);
  }
  .back-mark {
    position: absolute;
    left: 0; right: 0; top: 118px;
    display: flex; align-items: center; justify-content: center; gap: 14px;
  }
  .mark-dot {
    width: 34px; height: 34px; border-radius: 50%;
    background: var(--ink);
  }
  .back-mark .brand-name {
    font-size: 34px; font-weight: 700; color: var(--ink); letter-spacing: 1px;
  }
  .back-rule {
    position: absolute; left: 150px; top: 232px;
    width: 220px; height: 1px; background: var(--ink-soft);
  }
  /* Front face */
  .card--front {
    left: 630px;
    background: var(--card-white);
  }
  .edge-tab {
    position: absolute; width: 10px; height: 70px;
    background: linear-gradient(90deg, var(--silver-dark), var(--silver-light));
  }
  .edge-tab--left { left: 0; bottom: 26px; }
  .edge-tab--right { right: 0; top: 26px; transform: scaleX(-1); }
  .front-logo {
    position: absolute; left: 44px; top: 62px;
    display: flex; align-items: center; gap: 12px;
  }
  .front-logo .mark-dot { width: 26px; height: 26px; background: var(--ink-soft); }
  .front-logo .brand-name {
    font-size: 36px; font-weight: 700; color: var(--ink-soft); letter-spacing: 1px;
  }
  .holder {
    position: absolute; left: 44px; top: 168px;
    text-align: right; width: 190px;
  }
  .holder-name { font-size: 18px; font-weight: 700; color: var(--ink); margin-bottom: 8px; }
  .holder-address { font-size: 12.5px; color: var(--ink-faint); line-height: 1.55; }
  .contact-list {
    position: absolute; left: 262px; top: 168px;
    list-style: none;
  }
  .contact-list li {
    display: flex; align-items: center; gap: 9px;
    font-size: 12.5px; color: var(--ink-faint); margin-bottom: 9px;
  }
  .contact-list svg { width: 13px; height: 13px; fill: var(--ink); flex: none; }
</style>
</head>
<body>
  <section class="card card--back" aria-label="Card back">
    <div class="back-mark">
      <span class="mark-dot"></span>
      <span class="brand-name">Brisk Inquiries</span>
    </div>
    <div class="back-rule"></div>
  </section>

  <section class="card card--front" aria-label="Card front">
    <span class="edge-tab edge-tab--left"></span>
    <span class="edge-tab edge-tab--right"></span>

    <div class="front-logo">
      <span class="brand-name">Brisk Inquiries</span>
      <span class="mark-dot"></span>
    </div>

    <div class="holder">
      <p class="holder-name">Morgan Kellaway</p>
      <p class="holder-address">PO Box 58<br>Carnwell NSW 2291</p>
    </div>

    <ul class="contact-list">
      <li>
        <svg viewBox="0 0 16 16" aria-hidden="true"><path d="M3 1h3l1.5 4-2 1.3a9 9 0 0 0 4.2 4.2L11 8.5l4 1.5v3a2 2 0 0 1-2 2A12 12 0 0 1 1 3a2 2 0 0 1 2-2z"/></svg>
        0487 316 204
      </li>
      <li>
        <svg viewBox="0 0 16 16" aria-hidden="true"><path d="M1 3h14v10H1z M2 4l6 5 6-5" fill="none" stroke="#2e2e2e" stroke-width="1.6"/></svg>
        info@briskinquiries-demo.com.au
      </li>
      <li>
        <svg viewBox="0 0 16 16" aria-hidden="true"><circle cx="8" cy="8" r="7"/><path d="M1 8h14M8 1c3 3 3 11 0 14M8 1c-3 3-3 11 0 14" fill="none" stroke="#fff" stroke-width="1"/></svg>
        www.briskinquiries-demo.com.au
      </li>
    </ul>
  </section>
</body>
</html>
```